Irrigation Business needs their business cards modernised and revamped

I would like to keep my current logo, colours and revamp the format of the card.

I would like the card to be clean yet important.

Im not sure if you include texture but i would like the named logo to be indented into the card etc.

show me something alive and free something thats clinical to the point yet has a feel of achievement. i would like people to go nice card.

Target Market(s)

high end clients, corporate, sports field manger, the guys that make the decisions

Industry/Entity Type

Business

Contact Information for Business Card

nformation to be included

Dean Harlow (Director)
0487305526
dean@kolvat.biz
www.kestonfieldworks.com

instagram logo
google logo
facebook logo

Colors

Designer to choose colors to be used in the design.

Requirements
Nice to have
• indentations a really nice feel to the card good texture

```html
<!DOCTYPE html>
<html lang="en">
<head>
<meta charset="utf-8">
<title>Keston Fieldworks – Business Card</title>
<link href="https://fonts.googleapis.com/css2?family=Open+Sans:wght@400;700;800&display=swap" rel="stylesheet">
<style>
  :root{
    --bg:#2c2c2e;
    --green-light:#6ce3b3;
    --green-dark:#3aa86b;
    --blue:#2d69b4;
    --blue-light:#4a86c8;
    --sky:#39a6dc;
    --paper:#f4f4f3;
    --white:#ffffff;
  }
  *{margin:0;padding:0;box-sizing:border-box}
  html,body{width:1200px;height:840px;overflow:hidden;background:var(--bg)}
  body{font-family:"Open Sans",Arial,sans-serif;position:relative}
  .card{position:absolute;left:280px;width:640px;height:366px;overflow:hidden;box-shadow:0 14px 30px rgba(0,0,0,.45)}
  .card--front{top:36px;background:linear-gradient(100deg,var(--green-light) 0%,var(--green-dark) 62%,#3fac6f 100%)}
  .card--back{top:438px;background:var(--paper)}

  .front-brand{position:absolute;left:0;right:0;top:118px;display:flex;align-items:center;justify-content:center;gap:16px}
  .front-brand__dot{width:54px;height:54px;border:5px solid var(--white);border-radius:50%}
  .front-brand__name{color:var(--white);font-weight:800;font-size:30px;letter-spacing:1px;text-transform:uppercase}
  .social{position:absolute;left:352px;top:250px;display:flex;gap:8px}
  .social__item{width:20px;height:20px;border-radius:50%;background:var(--white)}

  .back-band{position:absolute;left:0;right:0;top:212px;bottom:0;background:linear-gradient(100deg,var(--blue) 0%,var(--blue-light) 45%,var(--blue) 100%)}
  .back-brand{position:absolute;left:40px;top:118px;display:flex;align-items:center;gap:12px}
  .back-brand__dot{width:52px;height:52px;border-radius:50%;background:var(--sky);border:3px solid var(--blue)}
  .back-brand__name{color:var(--blue);font-weight:800;font-size:24px;text-transform:uppercase;letter-spacing:.5px}
  .back-mark{position:absolute;left:560px;top:186px;width:52px;height:52px;border-radius:50%;background:var(--sky);border:3px solid var(--white)}

  .contact{position:absolute;left:40px;top:234px;color:var(--white)}
  .contact__name{font-weight:700;font-size:17px;text-transform:uppercase;letter-spacing:.3px}
  .contact__role{font-size:14px;text-transform:uppercase;margin-bottom:10px}
  .contact__line{display:flex;align-items:center;gap:9px;font-size:14px;line-height:21px}
  .contact__line svg{width:12px;height:12px;flex:none}
</style>
</head>
<body>
  <section class="card card--front">
    <div class="front-brand">
      <span class="front-brand__dot"></span>
      <span class="front-brand__name">Keston Fieldworks</span>
    </div>
    <div class="social" role="img" aria-label="Social media links">
      <span class="social__item"></span>
      <span class="social__item"></span>
      <span class="social__item"></span>
    </div>
  </section>

  <section class="card card--back">
    <div class="back-band"></div>
    <div class="back-brand">
      <span class="back-brand__dot"></span>
      <span class="back-brand__name">Keston Fieldworks</span>
    </div>
    <span class="back-mark"></span>
    <div class="contact">
      <p class="contact__name">Dean Harlow</p>
      <p class="contact__role">Director</p>
      <p class="contact__line">
        <svg viewBox="0 0 12 12" aria-hidden="true"><path fill="#fff" d="M2.4 1h2l1 2.6-1.3.9a6.5 6.5 0 0 0 3.4 3.4l.9-1.3L11 7.6v2c0 .8-.6 1.4-1.4 1.4A9.6 9.6 0 0 1 1 2.4C1 1.6 1.6 1 2.4 1z"/></svg>
        0487305526
      </p>
      <p class="contact__line">
        <svg viewBox="0 0 12 12" aria-hidden="true"><rect x="1" y="2.5" width="10" height="7" rx="1" fill="#fff"/><path d="M1.5 3l4.5 3.5L10.5 3" stroke="#2d69b4" stroke-width="1" fill="none"/></svg>
        dean@kolvat.biz
      </p>
      <p class="contact__line">
        <svg viewBox="0 0 12 12" aria-hidden="true"><circle cx="6" cy="6" r="5" fill="#fff"/><path d="M1 6h10M6 1c2 2.5 2 7.5 0 10M6 1c-2 2.5-2 7.5 0 10" stroke="#2d69b4" stroke-width=".8" fill="none"/></svg>
        www.kestonfieldworks.com
      </p>
    </div>
  </section>
</body>
</html>
```